KOVA! Card

The single side "business card" will be utilized to write down product information for our customers. The card needs to include our logo in josefin font and read KOVA! on the front. Our brand colors are espresso brown and copper. The back needs to be white (blank) to allow us to write information down. We want modern, bold, clean and fun.
I have attached a copy of our logo but you do not have to utilize exactly as shown.

```html
<!DOCTYPE html>
<html lang="en">
<head>
<meta charset="utf-8">
<title>KOVA! Card</title>
<link href="https://fonts.googleapis.com/css2?family=Josefin+Sans:wght@400;600&display=swap" rel="stylesheet">
<style>
  :root {
    --backdrop: #e8e6ea;
    --espresso: #2a1810;
    --copper: #c96a20;
    --ink: #2a1810;
  }
  html, body {
    margin: 0;
    padding: 0;
    width: 1200px;
    height: 900px;
    overflow: hidden;
    background: var(--backdrop);
  }
  .canvas {
    position: relative;
    width: 1200px;
    height: 900px;
  }
  .card {
    position: absolute;
    left: 380px;
    top: 65px;
    width: 440px;
    height: 770px;
    background: var(--espresso);
    overflow: hidden;
    font-family: "Josefin Sans", sans-serif;
  }
  .card__brand {
    position: absolute;
    left: 62px;
    top: 150px;
    margin: 0;
    font-weight: 400;
  }
  .card__name {
    display: block;
    font-size: 64px;
    font-weight: 400;
    line-height: 1;
    letter-spacing: 6px;
    text-transform: uppercase;
    color: var(--copper);
  }
  .card__tagline {
    display: block;
    margin-top: 18px;
    font-size: 24px;
    font-weight: 400;
    letter-spacing: 1px;
    color: var(--copper);
  }
  .card__band {
    position: absolute;
    left: 0;
    right: 0;
    bottom: 0;
    height: 120px;
    background: var(--copper);
  }
  .card__callout {
    position: absolute;
    right: 40px;
    bottom: 42px;
    margin: 0;
    font-size: 36px;
    font-weight: 600;
    letter-spacing: 4px;
    line-height: 1;
    color: var(--ink);
  }
</style>
</head>
<body>
  <main class="canvas">
    <article class="card">
      <h1 class="card__brand">
        <span class="card__name">halvers</span>
        <span class="card__tagline">Gift &amp; Craft Atelier</span>
      </h1>
      <div class="card__band"></div>
      <p class="card__callout">KOVA!</p>
    </article>
  </main>
</body>
</html>
```